New Bicycle shop business card

Hi!
I'm looking for a business card for my new proffesional bike mechanics shop. This shop is only for fixing broken bikes and not selling bikes.
Peferbly a modern and sleek and modern design.
Colors: black, grey, red, white
Information:
Name: Rijwielwerkplaats Vanhoutte
Shop owner: Bart Vanhoutte & Marieke Segers
Website: www.rijwielwerkplaats-vanhoutte.be
Email: info@rijwielwerkplaats-vanhoutte.be
Phone number: +32471902368
Street adres: Kerkweg 46
9940 Bellebeke
Slogan/shop information: Herstellingen van alle merken.
Logo: see files.
Target Market(s)
People who seek a mechanic to fix or upgrade their bikes.
Contact Information for Business Card
Information:
Website: info@rijwielwerkplaats-vanhoutte.be
9940 Bellebeke
Logo: see files.

```html
<!DOCTYPE html>
<html lang="nl">
<head>
<meta charset="utf-8">
<title>Rijwielwerkplaats Vanhoutte – visitekaartje</title>
<link href="https://fonts.googleapis.com/css2?family=Montserrat:wght@700;800&family=Roboto:wght@400&display=swap" rel="stylesheet">
<style>
  :root{
    --red:#d8263a;
    --black:#1b1b1b;
    --grey:#8e9296;
    --light-grey:#b9bcbf;
    --white:#ffffff;
    --backdrop:#e6e6e6;
  }
  *{box-sizing:border-box;margin:0;padding:0}
  html,body{width:1200px;height:852px;overflow:hidden}
  body{background:var(--backdrop);position:relative;font-family:'Roboto',sans-serif}

  .card{
    position:absolute;top:251px;width:540px;height:350px;
    background:var(--white);border-radius:20px;overflow:hidden;
    box-shadow:0 8px 22px rgba(0,0,0,.18);
  }
  .card--front{left:40px}
  .card--back{left:620px}

  .brand{display:flex;align-items:center;gap:12px}
  .brand__mark{width:30px;height:30px;border-radius:50%;background:var(--red);flex:none}
  .brand__name{
    font-family:'Montserrat',sans-serif;font-weight:800;color:var(--black);
    text-transform:uppercase;font-size:24px;line-height:1.05;letter-spacing:.5px;
  }

  /* front */
  .card--front .brand{position:absolute;left:0;right:0;top:105px;justify-content:center}
  .tagline{
    position:absolute;left:0;right:0;top:208px;display:flex;align-items:center;
    justify-content:center;gap:14px;font-size:14px;color:var(--black);
  }
  .tagline::before,.tagline::after{content:"";width:46px;height:2px;background:var(--red)}
  .front-band{position:absolute;left:0;bottom:0;width:540px;height:14px}

  /* back */
  .card--back .brand{position:absolute;left:28px;top:112px;gap:10px}
  .card--back .brand__mark{width:26px;height:26px}
  .card--back .brand__name{font-size:17px}
  .person{position:absolute;right:26px;top:30px;text-align:right}
  .person__name{font-family:'Montserrat',sans-serif;font-weight:700;color:var(--red);font-size:20px;text-transform:uppercase;letter-spacing:.5px}
  .person__role{font-size:12px;color:var(--black);margin-top:3px}
  .wave{position:absolute;left:0;top:0;width:540px;height:350px}
  .contact{position:absolute;right:22px;top:178px;list-style:none;text-align:right}
  .contact__item{
    display:flex;justify-content:flex-end;align-items:center;gap:8px;
    color:var(--white);font-size:12px;height:24px;
  }
  .contact__icon{width:12px;height:12px;fill:var(--white);flex:none}
</style>
</head>
<body>

<section class="card card--front" aria-label="Voorzijde">
  <div class="brand">
    <span class="brand__mark"></span>
    <span class="brand__name">Rijwielwerkplaats<br>Vanhoutte</span>
  </div>
  <p class="tagline">Herstellingen van alle merken</p>
  <svg class="front-band" viewBox="0 0 540 14" preserveAspectRatio="none" aria-hidden="true">
    <polygon points="0,0 300,0 290,14 0,14" fill="var(--red)"/>
    <polygon points="300,0 540,0 540,14 290,14" fill="var(--grey)"/>
  </svg>
</section>

<section class="card card--back" aria-label="Achterzijde">
  <svg class="wave" viewBox="0 0 540 350" aria-hidden="true">
    <path d="M0,338 C150,342 250,300 295,222 C343,140 440,108 540,102 L540,350 L0,350 Z" fill="var(--red)"/>
    <path d="M0,322 C150,328 240,290 287,212 C335,130 435,96 540,90" fill="none" stroke="var(--light-grey)" stroke-width="9"/>
    <path d="M170,314 C230,302 265,270 280,240 C325,140 420,92 540,80" fill="none" stroke="var(--black)" stroke-width="4"/>
  </svg>

  <div class="person">
    <p class="person__name">Marieke Segers</p>
    <p class="person__role">Owner</p>
  </div>

  <div class="brand">
    <span class="brand__mark"></span>
    <span class="brand__name">Rijwielwerkplaats<br>Vanhoutte</span>
  </div>

  <ul class="contact">
    <li class="contact__item">+32471902368
      <svg class="contact__icon" viewBox="0 0 24 24"><path d="M6.6 10.8a15 15 0 0 0 6.6 6.6l2.2-2.2a1 1 0 0 1 1-.25 11 11 0 0 0 3.6.6 1 1 0 0 1 1 1V20a1 1 0 0 1-1 1A17 17 0 0 1 3 4a1 1 0 0 1 1-1h3.5a1 1 0 0 1 1 1 11 11 0 0 0 .6 3.6 1 1 0 0 1-.25 1z"/></svg></li>
    <li class="contact__item">rijwielwerkplaats-vanhoutte.be
      <svg class="contact__icon" viewBox="0 0 24 24"><path d="M12 2a10 10 0 1 0 0 20 10 10 0 0 0 0-20zm6.9 6h-3a15 15 0 0 0-1.3-4A8 8 0 0 1 18.9 8zM12 4a13 13 0 0 1 1.9 4h-3.8A13 13 0 0 1 12 4zM4.3 14a8 8 0 0 1 0-4h3.4a16 16 0 0 0 0 4zm.8 2h3a15 15 0 0 0 1.3 4A8 8 0 0 1 5.1 16zm3-8h-3a8 8 0 0 1 4.3-4 15 15 0 0 0-1.3 4zM12 20a13 13 0 0 1-1.9-4h3.8A13 13 0 0 1 12 20zm2.3-6H9.7a14 14 0 0 1 0-4h4.6a14 14 0 0 1 0 4zm.3 6a15 15 0 0 0 1.3-4h3a8 8 0 0 1-4.3 4zm1.7-6a16 16 0 0 0 0-4h3.4a8 8 0 0 1 0 4z"/></svg></li>
    <li class="contact__item">info@rijwielwerkplaats-vanhoutte.be
      <svg class="contact__icon" viewBox="0 0 24 24"><path d="M2 5h20v14H2zm2 2v.5l8 5 8-5V7l-8 5z"/></svg></li>
    <li class="contact__item">Kerkweg 46 9940 Bellebeke
      <svg class="contact__icon" viewBox="0 0 24 24"><path d="M12 2a7 7 0 0 0-7 7c0 5 7 13 7 13s7-8 7-13a7 7 0 0 0-7-7zm0 9.5A2.5 2.5 0 1 1 12 6.5a2.5 2.5 0 0 1 0 5z"/></svg></li>
  </ul>
</section>

</body>
</html>
```